Tide & Thistle Website Creation For Online Spirits Sales via MerrowVats.com

Want a Website developed that I will use to partner with Merrow Vats to sell my signature rum online. Merrow Vats will add the final code to make the website an e-commerce site. Website should have links to Social media pages, recipies, About, news and events, products. I have he domain name already just need a designer to make the website look professional. Need website capable of being viewed on iPhone and Android devices. Please use the color scheme that is on the label. The brand motto is: Celebrate Life With Family old and new friends. The bottle sent in the images will be replaced with and actual high resolution image of the bottle when it is produce on 27 DEC 21. Can give the selected designer access to develop the website. I have the hostbramble.com domain name. Final code will be added by a designer from MerrowVats.com to make it a e-commerce store.
Updates

I added more information to refine the design I wanted. I should have had this information available to the designers when I started the project.

Target Market(s)

Target Market is 25-50 year old who drink rum

Industry/Entity Type

Spirits. Using Website to sell Rum online

Number of Pages Required

1 page

Font styles to use
Sans Serif

Colors
00AB8E
00BBA5
67D7C9
C6EFE9
E9F9F6

Requirements
Must have
• Must look elegant and of high class. Rum is being market as a premium unnamed rum.
Nice to have
• Video of people drinking, smiling and celebrating

```html
<!DOCTYPE html>
<html lang="en">
<head>
<meta charset="utf-8">
<title>Tide &amp; Thistle</title>
<link href="https://fonts.googleapis.com/css2?family=Oswald:wght@400;500;600&family=Lato:wght@400;700&display=swap" rel="stylesheet">
<style>
:root{
  --teal:#00AB8E;
  --teal-2:#00BBA5;
  --teal-3:#67D7C9;
  --mint:#C6EFE9;
  --mint-pale:#E9F9F6;
  --ink:#222;
  --text:#444;
  --dark:#1b1b1b;
  --white:#fff;
}
*{margin:0;padding:0;box-sizing:border-box}
html,body{width:1200px;height:2924px;overflow:hidden}
body{font-family:'Lato',sans-serif;color:var(--text);background:var(--white)}
.heading{font-family:'Oswald',sans-serif;font-weight:500;color:var(--ink);text-transform:uppercase}
.btn{display:inline-block;background:var(--teal);color:var(--white);font-family:'Oswald',sans-serif;font-size:20px;letter-spacing:1px;padding:16px 34px;text-transform:uppercase}
.dots{display:flex;gap:12px}
.dots span{width:10px;height:10px;border-radius:50%;background:#ccc}
.dots span.on{background:var(--teal)}

/* Header */
.site-header{height:140px;position:relative;display:flex;align-items:center;padding:0 48px}
.nav{display:flex;gap:34px;font-family:'Oswald',sans-serif;font-size:18px;text-transform:uppercase;color:var(--ink)}
.nav .active{color:var(--teal)}
.nav-right{margin-left:auto;align-items:center}
.brand{position:absolute;left:50%;top:20px;transform:translateX(-50%);display:flex;flex-direction:column;align-items:center;gap:8px}
.brand-dot{width:54px;height:54px;border-radius:50%;background:var(--ink)}
.brand-name{font-family:'Oswald',sans-serif;font-weight:500;font-size:30px;color:var(--ink);letter-spacing:1px;text-transform:uppercase}
.user-icon{width:24px;height:24px}

/* Hero */
.hero{height:700px;position:relative;background:linear-gradient(180deg,#2f5f8c 0%,#7ea4c2 30%,#5b7a3a 55%,#2d4a1c 80%,#6a5230 100%);display:flex;flex-direction:column;align-items:center;text-align:center;padding-top:220px}
.hero-title{font-family:'Oswald',sans-serif;font-weight:500;color:var(--white);font-size:54px;line-height:1.2;text-transform:uppercase;letter-spacing:1px}
.hero-sub{color:var(--white);font-size:22px;line-height:1.4;margin:18px 0 30px;width:620px}
.hero .dots{position:absolute;bottom:80px;left:50%;transform:translateX(-50%)}
.hero .dots span{background:rgba(255,255,255,.6)}
.hero .dots span.on{background:var(--white)}

/* About */
.about{height:580px;background:linear-gradient(135deg,#ececec,#dcdcdc);position:relative}
.about-bottles{position:absolute;left:160px;top:60px;width:330px;height:460px;background:linear-gradient(180deg,#d9b47a,#b07a34);border-radius:30px 30px 10px 10px}
.about-copy{position:absolute;left:520px;top:100px;width:600px}
.about-copy .heading{font-size:46px}
.about-lead{font-family:'Lato',sans-serif;font-weight:700;color:var(--teal);font-size:22px;line-height:1.35;margin:14px 0 14px}
.about-copy p.body{font-size:16px;line-height:1.55;margin-bottom:8px}
.about-copy .btn{margin-top:30px}

/* Recipes */
.recipes{height:560px;background:var(--mint-pale);padding-top:40px}
.recipes>.heading{text-align:center;font-size:48px}
.recipe-grid{display:flex;gap:36px;justify-content:center;margin-top:40px}
.recipe-card{width:328px;text-align:center}
.recipe-photo{height:200px;background:linear-gradient(135deg,#6b4a30,#3a2a1e 60%,#8a6a4a)}
.recipe-title{font-family:'Oswald',sans-serif;font-weight:600;color:var(--teal);font-size:22px;margin:34px 0 8px;text-transform:uppercase}
.recipe-card p{font-size:15px;line-height:1.5;padding:0 20px}

/* Testimonials */
.testimonials{height:520px;position:relative}
.video{position:absolute;left:72px;top:32px;width:516px;height:416px;background:linear-gradient(135deg,#5a4634,#2e241c 55%,#7a6450)}
.video svg{position:absolute;left:50%;top:50%;transform:translate(-50%,-50%)}
.testimonial-copy{position:absolute;left:612px;top:100px;width:540px}
.testimonial-copy .heading{font-size:48px}
.quote{font-size:20px;line-height:1.5;margin-top:24px;color:var(--ink)}
.author{color:var(--teal);font-size:16px;margin-top:14px}
.testimonials .dots{position:absolute;left:616px;top:434px}

/* Footer */
.site-footer{height:424px;background:var(--dark);color:var(--white);position:relative}
.footer-top{display:flex;align-items:center;padding:70px 72px 0}
.footer-brand{display:flex;flex-direction:column;align-items:center;gap:8px;width:200px}
.footer-brand .brand-dot{background:var(--white)}
.footer-brand .brand-name{color:var(--white)}
.divider{width:2px;height:110px;background:#666;margin:0 32px}
.subscribe{display:flex;align-items:center}
.subscribe .heading{color:var(--white);font-size:26px;margin-right:24px}
.email{width:390px;height:56px;background:var(--white);color:var(--ink);font-size:15px;font-weight:700;padding:18px;text-transform:uppercase}
.subscribe .btn{padding:16px 28px;height:56px}
.footer-nav{display:flex;justify-content:center;gap:34px;margin-top:74px;font-family:'Oswald',sans-serif;font-size:18px;text-transform:uppercase}
.copyright{text-align:center;font-size:14px;margin-top:16px;color:#ddd}
.social{display:flex;justify-content:center;gap:16px;margin-top:16px}
.social span{width:20px;height:20px;border-radius:50%;background:var(--white)}
</style>
</head>
<body>

<header class="site-header">
  <nav class="nav">
    <span class="active">Home</span><span>About</span><span>Products</span><span>Recipes</span>
  </nav>
  <div class="brand"><span class="brand-dot"></span><span class="brand-name">Tide &amp; Thistle</span></div>
  <nav class="nav nav-right">
    <span>News &amp; Events</span><span>Contact</span>
    <svg class="user-icon" viewBox="0 0 24 24" fill="#00AB8E"><circle cx="12" cy="7" r="5"/><path d="M2 24c0-6 4.5-10 10-10s10 4 10 10z"/></svg>
  </nav>
</header>

<section class="hero" role="img" aria-label="Sugarcane field with a dirt path under a blue sky">
  <h1 class="hero-title">Set up your e-commerce<br>with Tide &amp; Thistle</h1>
  <p class="hero-sub">The No. 1 solution for direct to consumer E-Commerce services within the Beverage industry.</p>
  <span class="btn">Read more</span>
  <div class="dots"><span class="on"></span><span></span><span></span><span></span></div>
</section>

<section class="about">
  <div class="about-bottles" role="img" aria-label="Three bottles of Tide &amp; Thistle rum"></div>
  <div class="about-copy">
    <h2 class="heading">About Tide &amp; Thistle</h2>
    <p class="about-lead">The pioneer of the white-label approach within the Direct To Consumer channel.</p>
    <p class="body">Tide &amp; Thistle offers custom e-commerce solutions for emerging and established brands looking to use technology as a tool for reaching new customers.</p>
    <p class="body">Tide &amp; Thistle fulfillment services operate through a national network of licensed retailers, shipping carriers, and customer service professionals to guarantee the best fulfillment and logistics practices.</p>
    <span class="btn">Read more</span>
  </div>
</section>

<section class="recipes">
  <h2 class="heading">Our Recipes</h2>
  <div class="recipe-grid">
    <article class="recipe-card">
      <div class="recipe-photo" role="img" aria-label="Friends sharing drinks at a bar"></div>
      <h3 class="recipe-title">Doloremque</h3>
      <p>Nemo enim ipsam voluptatem quia voluptas sit aspernatur aut odit aut fugit, sed quia consequ.</p>
    </article>
    <article class="recipe-card">
      <div class="recipe-photo" role="img" aria-label="Group toasting with glasses"></div>
      <h3 class="recipe-title">Doloremque</h3>
      <p>Nemo enim ipsam voluptatem quia voluptas sit aspernatur aut odit aut fugit, sed quia consequ.</p>
    </article>
    <article class="recipe-card">
      <div class="recipe-photo" role="img" aria-label="Friends celebrating with cocktails"></div>
      <h3 class="recipe-title">Doloremque</h3>
      <p>Nemo enim ipsam voluptatem quia voluptas sit aspernatur aut odit aut fugit, sed quia consequ.</p>
    </article>
  </div>
</section>

<section class="testimonials">
  <div class="video" role="img" aria-label="Video of friends laughing and toasting">
    <svg width="96" height="96" viewBox="0 0 96 96"><circle cx="48" cy="48" r="44" fill="none" stroke="#fff" stroke-width="6"/><path d="M38 28 L68 48 L38 68 Z" fill="#fff"/></svg>
  </div>
  <div class="testimonial-copy">
    <h2 class="heading">Testimonials</h2>
    <p class="quote">“We would probably not be where we are today had it not been for Tide &amp; Thistle partnership”.</p>
    <p class="author">Marisol T.</p>
  </div>
  <div class="dots"><span class="on"></span><span></span><span></span><span></span></div>
</section>

<footer class="site-footer">
  <div class="footer-top">
    <div class="footer-brand"><span class="brand-dot"></span><span class="brand-name">Tide &amp; Thistle</span></div>
    <span class="divider"></span>
    <div class="subscribe">
      <span class="heading">Subscribe Email</span>
      <span class="email">Email address</span>
      <span class="btn">Subscribe</span>
    </div>
  </div>
  <nav class="footer-nav"><span>Home</span><span>About</span><span>Products</span><span>Recipes</span><span>News &amp; Events</span><span>Contact</span></nav>
  <p class="copyright">© Copyright 2021. CompanyName All rights reserved.</p>
  <div class="social"><span></span><span></span><span></span><span></span><span></span></div>
</footer>

</body>
</html>
```